Brindle Yard Care. The best in the biz

I run a lawn care service that offers full service mowing. 100% satisfaction guarantee. Fast, Friendly, quality service "I am your lawns best friend" I cut residential lawns. I offer a mow package that includes trimming, edging and clean up. Prices very from 20 dollars to 75. I want my logo to stand out. Free estimates

Target Market(s)

Home owners

Industry/Entity Type

Landscaping

Contact Information for Business Card

555-812-4473 tomvale48@quillmail.net Derek. Brindle Yard care

Colors
f37122
9bcb3c
cadf82

Requirements
Must have
• Company name.
• Phone number
• Email
• My services
• images
Nice to have
• A sun that is growing grass.
Should not have
• Incorrect information

```html
<!DOCTYPE html>
<html lang="en">
<head>
<meta charset="utf-8">
<title>Brindle Yard Care – Business Card</title>
<link rel="stylesheet" href="https://fonts.googleapis.com/css2?family=Open+Sans:wght@400;600&display=swap">
<style>
  :root {
    --backdrop: #4b433e;
    --card: #141414;
    --card-edge: #242424;
    --green: #9bcb3c;
    --green-light: #cadf82;
    --green-deep: #2f6a12;
    --orange: #f37122;
    --gold: #f2c01c;
    --text: #e8e8e8;
    --silver: #d9d9d9;
    --rule: #6a6a6a;
  }
  * { box-sizing: border-box; margin: 0; padding: 0; }
  html, body { width: 1200px; height: 814px; overflow: hidden; }
  body {
    background: var(--backdrop);
    font-family: "Open Sans", Arial, sans-serif;
    position: relative;
  }
  .card {
    position: absolute;
    width: 540px;
    height: 310px;
    background: var(--card);
    border: 1px solid var(--card-edge);
    border-radius: 4px;
    overflow: hidden;
  }
  .card--front { left: 50px; top: 252px; }
  .card--back { left: 610px; top: 252px; }

  /* front */
  .brand-mark {
    position: absolute;
    left: 34px;
    top: 58px;
    width: 170px;
    display: flex;
    flex-direction: column;
    align-items: center;
    gap: 12px;
  }
  .brand-mark__dot {
    width: 96px;
    height: 96px;
    border-radius: 50%;
    background: var(--orange);
  }
  .brand-mark__name {
    color: var(--text);
    font-weight: 600;
    font-size: 16px;
    white-space: nowrap;
  }
  .divider {
    position: absolute;
    left: 236px;
    top: 40px;
    width: 1px;
    height: 120px;
    background: var(--rule);
  }
  .contact {
    position: absolute;
    left: 258px;
    top: 44px;
    font-size: 13px;
    color: var(--text);
    line-height: 1.55;
  }
  .contact__name { color: var(--green); font-size: 17px; font-weight: 600; line-height: 1.2; }
  .contact__title { color: var(--gold); font-size: 13px; margin-bottom: 8px; }
  .contact__row { display: flex; align-items: center; gap: 8px; }
  .contact__row svg { width: 12px; height: 12px; flex: none; }
  .grass {
    position: absolute;
    left: 0; right: 0; bottom: 0;
    height: 96px;
    background: linear-gradient(to bottom, rgba(155,203,60,0) 0%, var(--green) 45%, var(--green-deep) 100%);
  }
  .services {
    position: absolute;
    left: 0; right: 0;
    bottom: 40px;
    text-align: center;
    font-size: 14px;
    color: var(--green-deep);
    font-weight: 600;
    letter-spacing: 0.3px;
  }

  /* back */
  .card--back .back-mark {
    position: absolute;
    inset: 0;
    display: flex;
    align-items: center;
    justify-content: center;
    gap: 16px;
  }
  .back-mark__dot {
    width: 54px; height: 54px; border-radius: 50%;
    background: var(--silver);
  }
  .back-mark__name {
    color: var(--silver);
    font-size: 34px;
    font-weight: 600;
  }
</style>
</head>
<body>
  <section class="card card--front">
    <div class="brand-mark">
      <span class="brand-mark__dot"></span>
      <span class="brand-mark__name">Brindle Yard Care</span>
    </div>
    <span class="divider"></span>
    <div class="contact">
      <p class="contact__name">Derek Vale</p>
      <p class="contact__title">CEO/Founder</p>
      <p>Derek. Brindle Yard care</p>
      <p class="contact__row">
        <svg viewBox="0 0 24 24" aria-hidden="true"><path fill="#9bcb3c" d="M6.6 10.8a15 15 0 0 0 6.6 6.6l2.2-2.2a1 1 0 0 1 1-.25 11.4 11.4 0 0 0 3.6.57 1 1 0 0 1 1 1V20a1 1 0 0 1-1 1A17 17 0 0 1 3 4a1 1 0 0 1 1-1h3.5a1 1 0 0 1 1 1c0 1.25.2 2.45.57 3.57a1 1 0 0 1-.25 1z"/></svg>
        555-812-4473
      </p>
      <p class="contact__row">
        <svg viewBox="0 0 24 24" aria-hidden="true"><rect x="2" y="5" width="20" height="14" rx="1.5" fill="#9bcb3c"/><path d="M2.5 6l9.5 7 9.5-7" fill="none" stroke="#141414" stroke-width="2"/></svg>
        tomvale48@quillmail.net
      </p>
    </div>
    <div class="grass" role="img" aria-label="Band of green grass blades along the bottom edge"></div>
    <p class="services">Trimming • edging • clean up</p>
  </section>

  <section class="card card--back">
    <div class="back-mark">
      <span class="back-mark__dot"></span>
      <span class="back-mark__name">Brindle Yard Care</span>
    </div>
  </section>
</body>
</html>
```